Stationery Set for Velmora Company

I need to create full stationery design for my company; Business Cards, Envelops, Letter Heads, Calendar.
In the letter head and Envelops... only contact information and website links.
Our company is a Service Management company with different domains of innovative services including Technology Service Management, Education Services, Outsourcing Management, Events Management.
I need a modern and innovative design specially for the business card. I some transparent designs and I like it, but don't limit your innovation to what I mentioned. Sky is limit for your innovation.

Target Market(s)

Middle East & Africa

Industry/Entity Type

Business Management

Colors
34a7d8
0355a3
85acd3
86cae7
cee9f5
cfdeed
e4daeb
f3f1f8
ecf7fb

Requirements
Must have
• Name, Title, Email, Mobile
Nice to have
• We have multiple locations in USA, KSA, EGY, so I need ideas about how to include all contact details maybe QR / Barcode or something else.
• Please see our locations and contact information: www.brightvelmora.example
Should not have
• Too much text

```html
<!DOCTYPE html>
<html lang="en">
<head>
<meta charset="utf-8">
<title>Velmora Company – Stationery Set</title>
<link rel="stylesheet" href="https://fonts.googleapis.com/css2?family=Open+Sans:wght@400;600;700&family=Michroma&display=swap">
<style>
  :root {
    --page-bg: #eeeff1;
    --paper: #ffffff;
    --brand-blue: #0355a3;
    --sky-blue: #34a7d8;
    --deep-blue: #2a3fa8;
    --mid-blue: #1f8fe0;
    --ink: #3c3c3c;
    --ink-soft: #6a6a6a;
    --on-blue: #ffffff;
  }
  * { box-sizing: border-box; margin: 0; padding: 0; }
  html, body { width: 1200px; height: 937px; overflow: hidden; }
  body {
    background: var(--page-bg);
    font-family: "Open Sans", Arial, sans-serif;
    color: var(--ink);
    position: relative;
  }
  .sheet {
    position: absolute;
    background: var(--paper);
    overflow: hidden;
    border-radius: 2px;
  }
  .accent-band {
    position: absolute; left: 0; bottom: 0; width: 100%;
    background: linear-gradient(90deg, var(--deep-blue) 0%, var(--mid-blue) 55%, var(--deep-blue) 100%);
  }
  .brand-name {
    position: absolute;
    font-family: "Open Sans", Arial, sans-serif;
    font-weight: 700;
    color: var(--brand-blue);
    white-space: nowrap;
    display: flex; align-items: center; gap: 5px;
  }
  .brand-dot { display: inline-block; border-radius: 50%; background: var(--sky-blue); }
  .web-link {
    position: absolute;
    font-family: "Michroma", Arial, sans-serif;
    color: var(--on-blue);
    letter-spacing: 0.12em;
    white-space: nowrap;
  }
  .contact-block {
    position: absolute;
    color: var(--on-blue);
    text-align: right;
    line-height: 1.55;
    white-space: nowrap;
  }

  /* Letterhead */
  .letterhead { left: 185px; top: 68px; width: 385px; height: 544px; }
  .letterhead .brand-name { left: 18px; top: 26px; font-size: 15px; }
  .letterhead .brand-dot { width: 8px; height: 8px; }
  .letter-body {
    position: absolute; left: 36px; top: 136px; width: 300px;
    font-size: 5.2px; line-height: 1.5; color: var(--ink-soft);
  }
  .letter-body p { margin-bottom: 6px; }
  .letter-body .gap { margin-bottom: 16px; }
  .letter-body strong { color: var(--ink); font-weight: 600; }
  .signature-area { width: 42px; height: 18px; background: #e4e6ea; margin: 4px 0; }
  .letterhead .accent-band { height: 100px; }
  .letterhead .contact-block { right: 22px; bottom: 14px; font-size: 5.6px; }

  /* Presentation folder */
  .folder { left: 633px; top: 40px; width: 461px; height: 576px; }
  .folder .brand-name { left: 136px; top: 265px; font-size: 26px; }
  .folder .brand-dot { width: 13px; height: 13px; }
  .folder .accent-band { height: 150px; }
  .folder .web-link { right: 20px; bottom: 12px; font-size: 10px; }

  /* Business cards */
  .card-front { left: 45px; top: 658px; width: 176px; height: 100px; border-radius: 6px; }
  .card-front .brand-name { left: 9px; top: 10px; font-size: 8.5px; gap: 3px; }
  .card-front .brand-dot { width: 5px; height: 5px; }
  .card-holder { position: absolute; right: 9px; top: 10px; text-align: right; line-height: 1.3; }
  .card-holder .holder-name { font-size: 6px; font-weight: 700; color: var(--ink); letter-spacing: 0.04em; }
  .card-holder .holder-title { font-size: 4.6px; color: var(--ink-soft); }
  .card-front .accent-band { height: 58px; }
  .card-front .contact-block { right: 9px; bottom: 6px; font-size: 3.8px; line-height: 1.5; }
  .card-back { left: 45px; top: 785px; width: 176px; height: 100px; border-radius: 6px; }
  .card-back .brand-name { left: 50%; top: 50%; transform: translate(-50%, -50%); font-size: 10px; gap: 4px; }
  .card-back .brand-dot { width: 6px; height: 6px; }

  /* Envelopes */
  .envelope-front { left: 265px; top: 671px; width: 438px; height: 209px; }
  .envelope-front .brand-name { left: 14px; top: 22px; font-size: 13px; }
  .envelope-front .brand-dot { width: 7px; height: 7px; }
  .envelope-front .accent-band { height: 80px; }
  .envelope-front .web-link { right: 22px; bottom: 12px; font-size: 8.5px; }
  .envelope-back { left: 737px; top: 671px; width: 431px; height: 209px; }
  .envelope-flap {
    position: absolute; left: 0; top: 0; width: 100%; height: 64px;
    border-radius: 0 0 30px 30px;
    background: linear-gradient(90deg, var(--deep-blue) 0%, var(--mid-blue) 55%, var(--deep-blue) 100%);
  }
  .envelope-back .web-link { left: 0; width: 100%; text-align: center; top: 27px; font-size: 10px; }
</style>
</head>
<body>

<!-- Letterhead -->
<section class="sheet letterhead">
  <div class="brand-name"><span class="brand-dot"></span>Velmora Company</div>
  <div class="letter-body">
    <p>July 2, 2012</p>
    <p><strong>Dear Sir,</strong><br>Cedar House, 12 Palm St., Dubai</p>
    <p class="gap">We are pleased to share our new service lines in technology, education, outsourcing and events management. Our teams in each region work closely with clients to plan, deliver and review every project with care and clear reporting.</p>
    <p class="gap">Please contact our office for a full schedule of meetings and service reviews this quarter.</p>
    <p>We look forward to continuing our partnership and to supporting your goals across the region. Our staff remain ready to answer any question and to arrange visits at your convenience.</p>
    <p>Best Regards,</p>
    <div class="signature-area" role="img" aria-label="Handwritten signature"></div>
    <p><strong>Samir Nour</strong><br>Director<br><br>Cedar House, 12 Palm St., Dubai</p>
  </div>
  <div class="accent-band" role="img" aria-label="Decorative blue and grey wave band"></div>
  <div class="contact-block">
    Level 16 Harbor Plaza<br>Cedar Road, Dubai<br>012 555 0147<br>012 555 0148<br>012 555 0149<br>hello@brightvelmora.example<br>www.brightvelmora.example
  </div>
</section>

<!-- Presentation folder -->
<section class="sheet folder">
  <div class="brand-name"><span class="brand-dot"></span>Velmora Company</div>
  <div class="accent-band" role="img" aria-label="Decorative blue and grey wave band"></div>
  <div class="web-link">www.brightvelmora.example</div>
</section>

<!-- Business card front -->
<section class="sheet card-front">
  <div class="brand-name"><span class="brand-dot"></span>Velmora Company</div>
  <div class="card-holder">
    <div class="holder-name">OMAR HADDAD</div>
    <div class="holder-title">Managing Director</div>
  </div>
  <div class="accent-band" role="img" aria-label="Decorative blue and grey wave band"></div>
  <div class="contact-block">
    Level 16 Harbor Plaza<br>Cedar Road, Dubai<br>012 555 0147<br>012 555 0148<br>hello@brightvelmora.example<br>www.brightvelmora.example
  </div>
</section>

<!-- Business card back -->
<section class="sheet card-back">
  <div class="brand-name"><span class="brand-dot"></span>Velmora Company</div>
</section>

<!-- Envelope front -->
<section class="sheet envelope-front">
  <div class="brand-name"><span class="brand-dot"></span>Velmora Company</div>
  <div class="accent-band" role="img" aria-label="Decorative blue and grey wave band"></div>
  <div class="web-link">www.brightvelmora.example</div>
</section>

<!-- Envelope back -->
<section class="sheet envelope-back">
  <div class="envelope-flap"></div>
  <div class="web-link">www.brightvelmora.example</div>
</section>

</body>
</html>
```